home accents e-commerce website

I'd like a professional simple website designed where I can sell my home goods. I already have my domain name registered. I need the website to accept credit card payments and Monvex. It should have a shopping cart option and calculate sales tax and shipping costs on merchandise automatically.

I'll be taking photographs of the merchandise and writing product descriptions myself. (I'm not a professional photographer, so these photos probably won't look too polished. If you can help me make them look better, that'd be great). As I add new merchandise in the future, I'd like an option where I can log in to the back end myself and add pictures/product descriptions. And take old products down as they sell out. So the website needs to be user-friendly for me, even though I'm completely web design illiterate!

I'd like a creative, talented person who can create a whimsical, cute website. Nothing too corporate-looking.

Thank you!

Target Market(s)

women, online shoppers, New York City-area, (ship products to the United States only)

Industry/Entity Type

Home And Garden

Coding

Coded - Design and coding required

Number of Pages Required

1 page

Font styles to use
Sans Serif

Colors
0355a3
ffffff

Requirements
Must have
• shopping cart feature
• safe, secure credit card and Monvex payments
• ability for me to go in and add new products and take down old/sold products
Nice to have
• whimsical, cute design
Should not have
• too corporate-looking

```html
<!DOCTYPE html>
<html lang="en">
<head>
<meta charset="utf-8">
<title>Nordale Home Goods</title>
<link href="https://fonts.googleapis.com/css2?family=Open+Sans:wght@400;600;700;800&display=swap" rel="stylesheet">
<style>
:root{
  --blue:#0355a3;
  --blue-dark:#02407a;
  --white:#ffffff;
  --ink:#333333;
  --muted:#888888;
  --line:#e2e2e2;
  --price:#0355a3;
  --old:#999999;
  --footer:#1f1f1f;
  --footer-2:#161616;
  --band:#8d8d8d;
  --bg:#ffffff;
}
*{box-sizing:border-box;margin:0;padding:0}
html,body{width:1200px;height:3076px;overflow:hidden;background:var(--bg)}
body{font-family:"Open Sans",Arial,sans-serif;color:var(--ink);font-size:14px}
.wrap{width:1000px;margin:0 auto;position:relative}

/* top bar */
.topbar{height:36px;border-bottom:1px solid var(--line)}
.topbar .wrap{display:flex;justify-content:flex-end;align-items:center;height:36px;gap:18px;font-size:12px;color:#555}
.topbar .item{display:flex;align-items:center;gap:6px}
.social{display:flex;gap:5px}
.social span{width:20px;height:20px;background:#444;display:block}

/* header */
.header{height:114px}
.header .wrap{display:flex;justify-content:space-between;align-items:center;height:114px}
.logo{color:#5f6f86;font-weight:800;line-height:1;text-transform:uppercase}
.logo .name{font-size:46px;letter-spacing:1px;display:block}
.logo .sub{font-size:15px;letter-spacing:6px;display:block;margin-top:4px}
.cart{display:flex;align-items:center;gap:6px;font-size:12px}
.cart .ico{width:30px;height:30px;border:1px solid #ccc;display:flex;align-items:center;justify-content:center}
.cart .count{border:1px solid #ccc;height:30px;padding:0 10px;display:flex;align-items:center}

/* nav */
.nav{height:40px;background:var(--blue)}
.nav .wrap{display:flex;align-items:center;height:40px}
.nav a{color:var(--white);text-decoration:none;font-size:12px;font-weight:600;padding:0 22px;height:40px;display:flex;align-items:center;text-transform:uppercase}
.nav a.active{background:var(--blue-dark)}
.search{margin-left:auto;display:flex;height:28px}
.search input{width:260px;border:none;padding:0 10px;font-family:inherit;font-size:12px}
.search button{width:34px;background:var(--blue-dark);border:1px solid var(--white);display:flex;align-items:center;justify-content:center}

/* top showcase */
.showcase{display:flex;gap:15px;margin-top:20px}
.categories{width:245px;height:352px;border:1px solid var(--line)}
.categories h3{background:#2d2d2d;color:var(--white);font-size:12px;font-weight:700;padding:10px 14px;display:flex;align-items:center;gap:8px}
.categories ul{list-style:none;padding:6px 14px}
.categories li{font-size:12px;color:#555;padding:7px 0;border-bottom:1px solid #f0f0f0}
.categories li:before{content:"› ";color:var(--muted)}
.hero{flex:1;height:442px;position:relative;background:linear-gradient(120deg,#d9d4cc 0%,#eeeae4 40%,#c8c2b8 100%)}
.hero .copy{position:absolute;right:40px;top:110px;color:var(--white);font-size:34px;font-weight:700;line-height:1.05;text-transform:uppercase;text-shadow:0 1px 2px rgba(0,0,0,.2)}
.hero .badge{position:absolute;right:40px;top:82px;width:70px;height:70px;border-radius:50%;background:var(--blue);color:var(--white);font-size:15px;font-weight:800;display:flex;align-items:center;justify-content:center;text-align:center;line-height:1}
.hero .shop{position:absolute;right:40px;top:255px;background:var(--blue);color:var(--white);font-size:14px;font-weight:700;padding:11px 24px}
.hero .dots{position:absolute;right:20px;bottom:14px;display:flex;gap:6px}
.hero .dots i{width:8px;height:8px;border-radius:50%;background:rgba(255,255,255,.7);display:block}

.banners{display:flex;gap:18px;margin-top:30px}
.banner{flex:1;height:210px;position:relative;display:flex;align-items:center;justify-content:center}
.banner span{position:relative;color:var(--white);font-size:24px;font-weight:700;text-transform:uppercase;text-shadow:0 1px 3px rgba(0,0,0,.35)}
.b1{background:linear-gradient(135deg,#c9bfae,#ece6dc)}
.b2{background:linear-gradient(135deg,#c9a27a,#e8d3b8)}
.b3{background:linear-gradient(135deg,#9b958d,#d8d2c9)}

.rule{height:1px;background:var(--line);margin:40px 0 0}

/* section heading */
.heading{text-align:center;font-size:36px;font-weight:400;color:#444;margin-top:40px}
.heading b{color:var(--blue);font-weight:400}
.tabs{display:flex;justify-content:center;gap:8px;margin-top:26px}
.tabs span{font-size:12px;padding:6px 18px;color:#444}
.tabs span.on{border:1px solid #bbb}

/* products */
.grid{display:grid;grid-template-columns:repeat(4,1fr);gap:30px 25px;margin-top:30px}
.card{border:1px solid var(--line);height:358px;position:relative;text-align:center}
.card .photo{height:222px;margin:6px}
.card .new{position:absolute;right:6px;top:6px;width:0;height:0;border-top:36px solid var(--blue);border-left:36px solid transparent}
.stars{display:flex;justify-content:center;gap:3px;margin-top:14px}
.stars i{width:11px;height:11px;background:#999;clip-path:polygon(50% 0,61% 35%,98% 35%,68% 57%,79% 91%,50% 70%,21% 91%,32% 57%,2% 35%,39% 35%)}
.stars i.off{background:#ddd}
.card .pname{font-size:13px;margin-top:10px}
.prices{font-size:14px;margin-top:12px;display:flex;justify-content:center;gap:16px}
.prices s{color:var(--old)}
.prices b{color:var(--price);font-weight:400}
.card.active{border-color:var(--blue)}
.actions{position:absolute;left:-1px;right:-1px;bottom:-34px;height:34px;display:flex;gap:2px}
.actions span{flex:1;background:#555;display:flex;align-items:center;justify-content:center}
.actions span.on{background:var(--blue)}
.viewall{display:block;width:190px;margin:62px auto 0;background:#2d2d2d;color:var(--white);text-align:center;font-size:14px;font-weight:600;padding:13px 0}

/* hot deals */
.deals{display:flex;gap:30px;margin-top:34px}
.deal{flex:1;display:flex;border:1px solid var(--line);height:228px}
.deal .photo{width:232px;margin:8px}
.deal .info{flex:1;padding:22px 18px}
.deal .stars{justify-content:flex-start;margin-top:0}
.deal .pname{font-size:13px;margin-top:10px}
.deal .prices{justify-content:flex-start;margin-top:8px}
.deal p{font-size:12px;color:var(--muted);line-height:1.5;margin-top:10px}

/* service band */
.band{background:var(--band);height:120px;margin-top:60px}
.band .wrap{display:flex;gap:16px;align-items:center;height:120px}
.feature{flex:1;background:var(--white);height:50px;display:flex;align-items:center;gap:12px;padding:0 14px;font-size:11px;color:#555;line-height:1.3}
.feature .ico{width:28px;height:28px;display:flex;align-items:center;justify-content:center}

/* footer */
.footer{background:var(--footer);height:325px;color:#bbb}
.footer .wrap{display:flex;padding-top:40px}
.f-about{width:360px}
.f-about .logo{color:var(--white)}
.f-about .logo .name{font-size:40px}
.f-about p{font-size:11px;line-height:1.6;margin-top:16px;width:320px}
.f-about .social{margin-top:16px}
.f-about .social span{background:#555}
.f-col{width:200px;margin-left:30px;padding-top:18px}
.f-col h4{color:var(--white);font-size:13px;font-weight:700;margin-bottom:14px}
.f-col li{list-style:none;font-size:11px;line-height:2}
.f-col.contact li{display:flex;gap:8px;align-items:flex-start}

.newsletter{background:var(--footer-2);height:90px;border-top:1px solid #333}
.newsletter .wrap{display:flex;align-items:center;height:90px}
.newsletter h4{color:var(--white);font-size:20px;font-weight:400;display:flex;align-items:center;gap:12px}
.newsletter .form{display:flex;margin-left:60px}
.newsletter input{width:360px;height:34px;border:none;padding:0 10px;font-family:inherit;font-size:12px}
.newsletter button{background:var(--blue);color:var(--white);border:none;font-family:inherit;font-weight:700;font-size:13px;padding:0 28px}
.newsletter .social{margin-left:auto}
.newsletter .social span{width:30px;height:30px;background:var(--white)}

.copyright{height:46px}
.copyright .wrap{display:flex;align-items:center;height:46px;font-size:12px;color:#555}
.pay{margin-left:auto;display:flex;gap:6px}
.pay span{border:1px solid #ccc;font-size:11px;font-weight:700;color:var(--blue);padding:3px 8px}
</style>
</head>
<body>

<div class="topbar"><div class="wrap">
  <div class="item"><svg width="12" height="12" viewBox="0 0 24 24"><path fill="#555" d="M6.6 10.8a15 15 0 006.6 6.6l2.2-2.2a1 1 0 011-.25 11 11 0 003.6.6 1 1 0 011 1V20a1 1 0 01-1 1A17 17 0 013 4a1 1 0 011-1h3.5a1 1 0 011 1 11 11 0 00.6 3.6 1 1 0 01-.25 1z"/></svg>+123 456 7890</div>
  <div class="item"><svg width="13" height="10" viewBox="0 0 26 20"><rect x="1" y="1" width="24" height="18" fill="none" stroke="#555" stroke-width="2"/><path d="M1 1l12 10L25 1" fill="none" stroke="#555" stroke-width="2"/></svg>info@nordalehome.com</div>
  <div class="social"><span></span><span></span><span></span><span></span></div>
</div></div>

<header class="header"><div class="wrap">
  <div class="logo"><span class="name">Nordale</span><span class="sub">Home Goods</span></div>
  <div class="cart">
    <div class="ico"><svg width="14" height="14" viewBox="0 0 24 24"><circle cx="12" cy="8" r="4" fill="#555"/><path d="M4 21a8 8 0 0116 0z" fill="#555"/></svg></div>
    <div class="ico"><svg width="14" height="14" viewBox="0 0 24 24"><path d="M12 21l-8-8a5 5 0 018-6 5 5 0 018 6z" fill="#555"/></svg></div>
    <div class="ico"><svg width="16" height="14" viewBox="0 0 26 22"><path d="M1 2h4l3 12h13l3-9H7" fill="none" stroke="#555" stroke-width="2"/><circle cx="10" cy="19" r="2" fill="#555"/><circle cx="19" cy="19" r="2" fill="#555"/></svg></div>
    <div class="count">0 items - $0.00</div>
  </div>
</div></header>

<nav class="nav"><div class="wrap">
  <a class="active">Home</a><a>About Nordale</a><a>How does this craziness work?</a><a>Contact Us</a>
  <div class="search"><input placeholder="Type Keyword..."><button><svg width="14" height="14" viewBox="0 0 24 24"><circle cx="10" cy="10" r="7" fill="none" stroke="#fff" stroke-width="3"/><path d="M15 15l7 7" stroke="#fff" stroke-width="3"/></svg></button></div>
</div></nav>

<main class="wrap">
  <section class="showcase">
    <aside class="categories">
      <h3><svg width="12" height="10" viewBox="0 0 12 10"><rect width="12" height="2" fill="#fff"/><rect y="4" width="12" height="2" fill="#fff"/><rect y="8" width="12" height="2" fill="#fff"/></svg>SHOP BY CATEGORIES</h3>
      <ul><li>Vases</li><li>Throw Pillows</li><li>Blankets and Throws</li><li>For Your Floors</li><li>For Your Walls</li><li>For Your Table</li><li>For Your Bedside</li><li>Let Things Be Light</li><li>Put Your Feet Up</li></ul>
    </aside>
    <div class="hero" role="img" aria-label="Bright living room with a white sofa and throw pillows">
      <div class="badge">20%<br>OFF</div>
      <div class="copy" style="right:130px">New<br>Look<br>Throw Pillows</div>
      <div class="shop">SHOP NOW »</div>
      <div class="dots"><i></i><i></i><i></i><i></i></div>
    </div>
  </section>

  <section class="banners">
    <div class="banner b1" role="img" aria-label="Ceramic vases on a shelf"><span>Vases</span></div>
    <div class="banner b2" role="img" aria-label="Stack of colourful throw pillows"><span>Throw Pillows</span></div>
    <div class="banner b3" role="img" aria-label="Blankets and throws on a bed"><span>Blankets and Throws</span></div>
  </section>

  <div class="rule"></div>

  <h2 class="heading">Featured <b>Products</b></h2>
  <div class="tabs"><span class="on">Latest</span><span>Best Seller</span><span>Special</span><span>New Arrival</span></div>

  <section class="grid">
    <div class="card"><div class="photo" role="img" aria-label="White patterned vases" style="background:linear-gradient(160deg,#f4f1ec,#e3ddd2)"></div><div class="stars"><i></i><i></i><i></i><i class="off"></i><i class="off"></i></div><div class="pname">Product Name 1</div><div class="prices"><s>$156.00</s><b>$156.00</b></div></div>
    <div class="card"><div class="photo" role="img" aria-label="Colourful throw pillows on a sofa" style="background:linear-gradient(160deg,#d9a25a,#9a5a4a)"></div><span class="new"></span><div class="stars"><i></i><i></i><i></i><i class="off"></i><i class="off"></i></div><div class="pname">Product Name 2</div><div class="prices"><s>$156.00</s><b>$156.00</b></div></div>
    <div class="card"><div class="photo" role="img" aria-label="Armchair with a knitted throw" style="background:linear-gradient(160deg,#c9bda8,#8d7f6a)"></div><div class="stars"><i></i><i></i><i></i><i class="off"></i><i class="off"></i></div><div class="pname">Product Name 3</div><div class="prices"><s>$156.00</s><b>$156.00</b></div></div>
    <div class="card"><div class="photo" role="img" aria-label="Bedroom with bedside lamp" style="background:linear-gradient(160deg,#e6e2dc,#b9b0a3)"></div><span class="new"></span><div class="stars"><i></i><i></i><i></i><i class="off"></i><i class="off"></i></div><div class="pname">Product Name 4</div><div class="prices"><s>$156.00</s><b>$156.00</b></div></div>
    <div class="card active"><div class="photo" role="img" aria-label="Candles on a table" style="background:linear-gradient(160deg,#ebe4d6,#b8a98f)"></div><div class="stars"><i></i><i></i><i></i><i class="off"></i><i class="off"></i></div><div class="pname">Product Name 1</div><div class="prices"><s>$156.00</s><b>$156.00</b></div>
      <div class="actions"><span><svg width="12" height="12" viewBox="0 0 24 24"><path d="M1 2h4l3 12h13l3-9H7" fill="none" stroke="#fff" stroke-width="2.5"/></svg></span><span><svg width="12" height="12" viewBox="0 0 24 24"><path d="M12 21l-8-8a5 5 0 018-6 5 5 0 018 6z" fill="#fff"/></svg></span><span><svg width="12" height="12" viewBox="0 0 24 24"><path d="M4 7h16M4 12h16M4 17h16" stroke="#fff" stroke-width="2.5"/></svg></span><span class="on"><svg width="12" height="12" viewBox="0 0 24 24"><circle cx="10" cy="10" r="7" fill="none" stroke="#fff" stroke-width="3"/><path d="M15 15l7 7" stroke="#fff" stroke-width="3"/></svg></span></div></div>
    <div class="card"><div class="photo" role="img" aria-label="Fireplace in a dark living room" style="background:linear-gradient(160deg,#6b4a35,#2e211a)"></div><div class="stars"><i></i><i></i><i></i><i class="off"></i><i class="off"></i></div><div class="pname">Product Name 2</div><div class="prices"><s>$156.00</s><b>$156.00</b></div></div>
    <div class="card"><div class="photo" role="img" aria-label="Large ceramic floor vase" style="background:linear-gradient(160deg,#d8d2c6,#9c917f)"></div><div class="stars"><i></i><i></i><i></i><i class="off"></i><i class="off"></i></div><div class="pname">Product Name 3</div><div class="prices"><s>$156.00</s><b>$156.00</b></div></div>
    <div class="card"><div class="photo" role="img" aria-label="Dark wooden side table" style="background:linear-gradient(160deg,#7a6a58,#3c3128)"></div><span class="new"></span><div class="stars"><i></i><i></i><i></i><i class="off"></i><i class="off"></i></div><div class="pname">Product Name 4</div><div class="prices"><s>$156.00</s><b>$156.00</b></div></div>
  </section>

  <a class="viewall">VIEW ALL »</a>

  <div class="rule" style="margin-top:58px"></div>

  <h2 class="heading">Hot <b>Deals</b></h2>
  <section class="deals">
    <div class="deal"><div class="photo" role="img" aria-label="Pink flowers in a glass vase" style="background:linear-gradient(160deg,#f3eef0,#d8b7c4)"></div><div class="info"><div class="stars"><i></i><i></i><i></i><i class="off"></i><i class="off"></i></div><div class="pname">Product Name 1</div><div class="prices"><s>$156.00</s><b>$156.00</b></div><p>Soft handmade vase with a matte glaze, perfect for fresh stems and cozy corners around the home.</p></div></div>
    <div class="deal"><div class="photo" role="img" aria-label="Patterned cushions on a grey sofa" style="background:linear-gradient(160deg,#b9b4aa,#6f6a62)"></div><div class="info"><div class="stars"><i></i><i></i><i></i><i class="off"></i><i class="off"></i></div><div class="pname">Product Name 2</div><div class="prices"><s>$156.00</s><b>$156.00</b></div><p>Cheerful patterned cushions that brighten any sofa, made from soft cotton with hidden zippers.</p></div></div>
  </section>
</main>

<section class="band"><div class="wrap">
  <div class="feature"><span class="ico"><svg width="26" height="18" viewBox="0 0 26 18"><rect x="1" y="2" width="15" height="11" fill="var(--blue)"/><path d="M16 6h5l4 4v3h-9z" fill="var(--blue)"/><circle cx="6" cy="15" r="2.5" fill="#555"/><circle cx="20" cy="15" r="2.5" fill="#555"/></svg></span><span><b style="background:var(--blue);color:#fff;padding:0 3px">FREE SHIPPING</b> On Order<br>Over $99</span></div>
  <div class="feature"><span class="ico"><svg width="20" height="20" viewBox="0 0 24 24"><path fill="#555" d="M6.6 10.8a15 15 0 006.6 6.6l2.2-2.2a1 1 0 011-.25 11 11 0 003.6.6 1 1 0 011 1V20a1 1 0 01-1 1A17 17 0 013 4a1 1 0 011-1h3.5a1 1 0 011 1 11 11 0 00.6 3.6 1 1 0 01-.25 1z"/></svg></span><span>Need help<br>+123 456 7890</span></div>
  <div class="feature"><span class="ico"><svg width="22" height="22" viewBox="0 0 24 24"><circle cx="12" cy="12" r="10" fill="none" stroke="#555" stroke-width="2"/><path d="M7 12l3 3 7-7" fill="none" stroke="#555" stroke-width="2"/></svg></span><span>Money Back Guarantee</span></div>
  <div class="feature"><span class="ico"><svg width="22" height="22" viewBox="0 0 24 24"><path d="M4 12a8 8 0 108-8H7" fill="none" stroke="#555" stroke-width="2"/><path d="M9 1L6 4l3 3" fill="none" stroke="#555" stroke-width="2"/></svg></span><span>30 Days Return Service</span></div>
</div></section>

<footer>
  <div class="footer"><div class="wrap">
    <div class="f-about">
      <div class="logo"><span class="name">Nordale</span><span class="sub">Home Goods</span></div>
      <p>We gather charming little pieces for every room, from soft throws to handmade vases. Each item is picked with love so your home feels warm, bright and just a bit playful every single day.</p>
      <div class="social"><span></span><span></span><span></span><span></span></div>
    </div>
    <div class="f-col"><h4>MY ACCOUNT</h4><ul><li>My Orders</li><li>My Credit Slips</li><li>My Addresses</li><li>My Personal Info</li></ul></div>
    <div class="f-col"><h4>INFORMATION</h4><ul><li>Specials</li><li>New Products</li><li>Best Sellers</li><li>Our Stores</li><li>Contact Us</li></ul></div>
    <div class="f-col contact"><h4>INFORMATION</h4><ul>
      <li><svg width="10" height="14" viewBox="0 0 10 14" style="margin-top:5px"><path d="M5 0a5 5 0 015 5c0 4-5 9-5 9S0 9 0 5a5 5 0 015-5z" fill="#bbb"/></svg><span>Nordale Home Goods<br>212 Maple Street<br>Brookfield, NY 10001</span></li>
      <li>+123 456 7890</li><li>info@nordalehome.com</li></ul></div>
  </div></div>
  <div class="newsletter"><div class="wrap">
    <h4><svg width="26" height="20" viewBox="0 0 26 20"><rect x="1" y="1" width="24" height="18" fill="none" stroke="#fff" stroke-width="2"/><path d="M1 1l12 10L25 1" fill="none" stroke="#fff" stroke-width="2"/></svg>Newsletter Signup</h4>
    <div class="form"><input placeholder="Enter your email"><button>SIGNUP</button></div>
    <div class="social"><span></span><span></span><span></span><span></span></div>
  </div></div>
  <div class="copyright"><div class="wrap">
    <span>Copyright © 2017 Nordale Home Goods. All Rights Reserved.</span>
    <div class="pay"><span>Cardwell</span><span>Veyra</span><span>Monvex</span><span>Orbipay</span></div>
  </div></div>
</footer>

</body>
</html>
```